Fitness Equipment & Service

I want to make the card eye catching and fun. We are called Corvane Motion Limited and we are based in Wales. We sell, install and service all types of fitness equipment from Skipping ropes, right through the Dumbbells, Kettle bells and Barbells through to state of the art Treadmills, Running Machines and Strength Equipment. We also design and install changing room furniture and lockers.

TYPOGRAPHY
We would like to use Futrura. Futura has an appearance of efficiency and forwardness. The typeface is derived
from simple geometric forms (near-perfect circles, triangles and squares) and is based on strokes of
near-even weight, which are low in contrast. This is most visible in the almost perfectly round stroke of
the o, which is nonetheless slightly ovoid.
The lowercase has tall ascenders, which rise above the cap line. The uppercase
characters present proportions similar to those of classical Roman capitals.

TYPOGRAPHIC CONSIDERATIONS
No Strike though
No Horizontal Scaling
No Drop Shadows
No Effects
Never use less than 120% Leading

OUR CORPORATE COLOURS
BRAND GUIDELINES
We were thinking that our primary colour palette consists of the Acid Green (Pantone 382) and Process Black.

We work closely with tquarly Ltd and would like to include their name on the card somewhere. I have attached images of the other brands that we work with as an idea or the small icons I have included that illustrate what we do?. I have very kindly been given permission to use any of the images off the files that I have included below, so I hope these help. I will include these below. I would be open to suggestions if it made the card more striking Can you do it?
Updates

Hi All, Just wanted to add a few thoughts but you are the guys with the creative visions (thats why are here) We are based in Wales, UK and we would be open to lots of different ideas on a theme but must be eye catching, Bold and FUN. If you can or think that the Welsh or any dragon could be put in there then go for it (its not a must have) We have also added some ideas for colour but again its over to you!! GO FOR IT ! Thanks and look forward to your visions! Owen

Hi All, Just thought I would sen through the contact details that need to be on the card. (if you want to play around with icons instead of the wording twitter, Facebook, go for it): Corvane Motion Limited Owen Pritchard Managing Director Mob: +44 (0)7582 913 406 e-mail: sales@corvanemotion.co.uk Web: Corvanemotion.co.uk twitter: @motionLetterbin Facebook: Corvane Motion Limited

```html
<!DOCTYPE html>
<html lang="en">
<head>
<meta charset="utf-8">
<title>Corvane Motion Limited – Business Card</title>
<link rel="stylesheet" href="https://fonts.googleapis.com/css2?family=Libre+Franklin:wght@700&family=Arimo:wght@400;700&display=swap">
<style>
  :root {
    --bg: #e6e4e0;
    --navy-deep: #15224f;
    --navy: #1f2f6b;
    --navy-light: #34477f;
    --gold: #b98f2c;
    --ink: #1e2a55;
    --grey-text: #4a4d57;
    --card-white: #ffffff;
    --map-tone: #e9ebef;
  }
  * { box-sizing: border-box; margin: 0; padding: 0; }
  html, body {
    width: 1200px; height: 950px; overflow: hidden;
    background: var(--bg);
    font-family: "Arimo", Arial, sans-serif;
  }
  .card {
    position: absolute; left: 240px;
    width: 720px; height: 410px;
    overflow: hidden;
    box-shadow: 0 6px 18px rgba(0,0,0,0.18);
  }

  /* Back side */
  .card-back {
    top: 45px;
    background: linear-gradient(90deg, var(--navy-deep) 0%, var(--navy) 45%, var(--navy) 74%, var(--navy-light) 80%, var(--navy-deep) 100%);
  }
  .card-back .brand {
    position: absolute; left: 0; right: 0; top: 130px;
    display: flex; flex-direction: column; align-items: center; gap: 18px;
  }
  .brand-dot {
    width: 110px; height: 110px; border-radius: 50%;
    background: #2b4f97;
  }
  .card-back .brand-name {
    font-weight: 700; font-size: 22px; letter-spacing: 1px;
    color: var(--gold); text-transform: uppercase;
  }
  .card-back .web {
    position: absolute; right: 40px; bottom: 34px;
    display: flex; align-items: center; gap: 8px;
    color: #c9cfe0; font-size: 17px; letter-spacing: 1px;
  }
  .card-back .web::after {
    content: ""; width: 60px; height: 1px; background: #c9cfe0;
  }

  /* Front side */
  .card-front {
    top: 495px;
    background: var(--card-white);
  }
  .map-area {
    position: absolute; left: 220px; top: 40px; width: 500px; height: 360px;
    background: radial-gradient(ellipse at 60% 50%, var(--map-tone) 0%, rgba(233,235,239,0.4) 55%, rgba(255,255,255,0) 80%);
  }
  .name-block {
    position: absolute; left: 0; top: 34px;
    display: flex; gap: 34px;
  }
  .name-bar { width: 14px; height: 62px; background: var(--navy-deep); }
  .person-name {
    font-family: "Libre Franklin", Arial, sans-serif; font-weight: 700;
    font-size: 26px; line-height: 1.2; color: var(--ink);
  }
  .person-role { font-size: 18px; line-height: 1.3; color: var(--gold); }
  .address {
    position: absolute; left: 48px; top: 128px;
    font-size: 18px; line-height: 1.35; color: var(--grey-text);
  }
  .contacts {
    position: absolute; left: 36px; top: 190px;
    list-style: none; font-size: 18px; line-height: 1.4; color: var(--grey-text);
  }
  .contacts li { display: flex; align-items: center; gap: 10px; }
  .contacts svg { width: 16px; height: 16px; flex: none; fill: var(--navy-deep); }
  .front-brand {
    position: absolute; right: 44px; bottom: 40px;
    display: flex; align-items: center; gap: 14px;
  }
  .front-brand .brand-dot { width: 90px; height: 90px; }
  .front-brand .brand-name {
    font-weight: 700; font-size: 19px; line-height: 1.25;
    color: var(--ink); text-transform: uppercase; letter-spacing: 0.5px;
  }
</style>
</head>
<body>
  <section class="card card-back">
    <div class="brand">
      <div class="brand-dot"></div>
      <div class="brand-name">Corvane Motion Limited</div>
    </div>
    <div class="web">corvanemotion.co.uk</div>
  </section>

  <section class="card card-front">
    <div class="map-area" role="img" aria-label="Faint world map background"></div>
    <div class="name-block">
      <div class="name-bar"></div>
      <div>
        <div class="person-name">Owen Pritchard</div>
        <div class="person-role">Managing Director</div>
      </div>
    </div>
    <div class="address">27 Harbour Lane<br>Llanbedr, LL45 2PX</div>
    <ul class="contacts">
      <li><svg viewBox="0 0 16 16"><path d="M4 0h8a1 1 0 0 1 1 1v14a1 1 0 0 1-1 1H4a1 1 0 0 1-1-1V1a1 1 0 0 1 1-1zm1 2v10h6V2zm3 11a1 1 0 1 0 0 2 1 1 0 0 0 0-2z"/></svg>+44 (0)7582 913 406</li>
      <li><svg viewBox="0 0 16 16"><path d="M0 3h16v10H0zm1.5 1.2L8 9l6.5-4.8V4h-13z"/></svg>sales@corvanemotion.co.uk</li>
      <li><svg viewBox="0 0 16 16"><circle cx="8" cy="8" r="8"/><path d="M1 8h14M8 1c-3 3-3 11 0 14M8 1c3 3 3 11 0 14" stroke="#fff" stroke-width="1" fill="none"/></svg>Corvanemotion.co.uk</li>
      <li><svg viewBox="0 0 16 16"><rect width="16" height="16" rx="2"/></svg>@motionLetterbin</li>
      <li><svg viewBox="0 0 16 16"><rect width="16" height="16" rx="2"/></svg>Corvane Motion Limited</li>
    </ul>
    <div class="front-brand">
      <div class="brand-dot"></div>
      <div class="brand-name">Corvane Motion<br>Limited</div>
    </div>
  </section>
</body>
</html>
```